KLV Plant Services

We are a heavy diesel mechanical business with additional air con certificates, remapping engine rebuilt

Contact Information for Business Card

Company Name, Director Name, Managing Director, Contact details, email and website

Font styles to use
Serif
Script

```html
<!DOCTYPE html>
<html lang="en">
<head>
<meta charset="utf-8">
<title>KLV Plant Services – Business Card</title>
<link href="https://fonts.googleapis.com/css2?family=Noto+Serif:wght@400;700&display=swap" rel="stylesheet">
<style>
  :root {
    --backdrop: #d6d6d6;
    --card: #f1f1f3;
    --navy: #1b1a66;
    --ink: #1a1a1a;
    --art: #2a2a2e;
  }
  * { box-sizing: border-box; margin: 0; padding: 0; }
  html, body { width: 1200px; height: 1051px; overflow: hidden; }
  body {
    background: var(--backdrop);
    font-family: "Noto Serif", Georgia, serif;
    color: var(--ink);
    position: relative;
  }
  .card {
    position: absolute;
    width: 530px;
    height: 303px;
    background: var(--card);
    border-bottom: 5px solid var(--navy);
    box-shadow: 0 18px 40px rgba(0,0,0,0.18);
    overflow: hidden;
  }
  .card--contact { left: 55px; top: 374px; }
  .card--brand { left: 615px; top: 374px; }

  .brand-name {
    font-family: "Noto Serif", Georgia, serif;
    font-weight: 700;
    color: var(--navy);
    display: flex;
    align-items: center;
    gap: 10px;
    line-height: 1.1;
  }
  .brand-mark {
    width: 14px; height: 14px;
    border-radius: 50%;
    background: var(--navy);
    flex: none;
  }
  .card--contact .brand-name {
    position: absolute; left: 32px; top: 30px;
    font-size: 18px;
  }
  .address {
    position: absolute; left: 32px; top: 78px;
    font-size: 13px; line-height: 1.35;
  }
  .contact-list {
    position: absolute; left: 32px; top: 128px;
    list-style: none;
    font-size: 13px; line-height: 1.55;
  }
  .contact-list li { display: flex; align-items: center; gap: 7px; }
  .contact-list svg { width: 11px; height: 11px; fill: var(--navy); flex: none; }

  .hero-art {
    position: absolute; left: 240px; bottom: 0;
    width: 190px; height: 92px;
    background: linear-gradient(160deg, var(--art), #000);
    opacity: 0.9;
  }
  .person {
    position: absolute; right: 44px; top: 138px;
    text-align: right;
    color: var(--navy);
    line-height: 1.3;
  }
  .person-name { font-size: 17px; font-weight: 700; letter-spacing: 0.5px; }
  .person-role { font-size: 13px; }
  .accent-band {
    position: absolute; right: 0; top: 140px;
    width: 26px; height: 44px;
    background: var(--navy);
  }

  .card--brand .brand-name {
    position: absolute; left: 0; right: 0; top: 50%;
    transform: translateY(-50%);
    justify-content: center;
    font-size: 38px;
    gap: 16px;
  }
  .card--brand .brand-mark { width: 26px; height: 26px; }
</style>
</head>
<body>
  <section class="card card--contact" aria-label="Business card back">
    <div class="brand-name"><span class="brand-mark"></span>KLV Plant Services</div>
    <p class="address">Your address, City<br>State, Zip 1234</p>
    <ul class="contact-list">
      <li><svg viewBox="0 0 24 24"><path d="M6.6 10.8a15 15 0 0 0 6.6 6.6l2.2-2.2a1 1 0 0 1 1-.25 11.4 11.4 0 0 0 3.6.57 1 1 0 0 1 1 1V20a1 1 0 0 1-1 1A17 17 0 0 1 3 4a1 1 0 0 1 1-1h3.5a1 1 0 0 1 1 1c0 1.25.2 2.45.57 3.57a1 1 0 0 1-.25 1z"/></svg>123 456 789</li>
      <li><svg viewBox="0 0 24 24"><path d="M2 5h20v14H2zm2 2v.5l8 5 8-5V7z"/></svg>info@yourgmail.com</li>
      <li><svg viewBox="0 0 24 24"><circle cx="12" cy="12" r="10"/></svg>www.yourwebsite.com</li>
    </ul>
    <div class="person">
      <div class="person-name">DANIEL HART</div>
      <div class="person-role">Managing Director</div>
    </div>
    <div class="accent-band"></div>
    <div class="hero-art" role="img" aria-label="Excavator arm and bucket silhouette"></div>
  </section>

  <section class="card card--brand" aria-label="Business card front">
    <div class="brand-name"><span class="brand-mark"></span>KLV Plant Services</div>
  </section>
</body>
</html>
```